Website for Briar Hollow Gathering Church

Wordpress website design required for Briar Hollow Gathering Church. We are a family oriented church catering for age groups from school age to elderly people. The church has a wide variety of activities which it coordinates. The idea is to describe the activities on the activities page, but cross-link them to show which would be applicable to the different age groups.

We would like an inviting website which is easy to read and navigate.

Target Market(s)

Very wide audience - from school age youth to elderly people, so design and style should cater for both audiences.

Industry/Entity Type

Church

Coding

Coded - Design and coding required

Number of Pages Required

5+ page

Font styles to use
Sans Serif

Colors
0255a3
ffffff
0792cd
f78f20

Requirements
Must have
• Inviting website.
• Clear readable font.
• Space to import photos to balance text on each page.
• Need to project a dynamic and progressive feel for the church.
• Easy to navigate.
Nice to have
• Scrolling photos on pages. Ability to enter questions/ comments/prayer requests on Home page.
Should not have
• Conservative audience, so should not be too bold.

```html
<!DOCTYPE html>
<html lang="en">
<head>
<meta charset="utf-8">
<title>Briar Hollow Gathering Church</title>
<link href="https://fonts.googleapis.com/css2?family=Arvo:wght@400;700&family=Open+Sans:wght@400;600;700&display=swap" rel="stylesheet">
<style>
:root{
  --blue-deep:#0255a3;
  --blue:#0792cd;
  --orange:#f78f20;
  --orange-dark:#e27612;
  --white:#ffffff;
  --ink:#333333;
  --muted:#6b6b6b;
  --nav-top:#2c2c2c;
  --nav-bottom:#0d0d0d;
  --footer:#1f1f1f;
  --footer-bottom:#151515;
  --footer-text:#8a8a8a;
}
*{box-sizing:border-box;margin:0;padding:0}
html,body{width:1200px;height:3462px;overflow:hidden}
body{font-family:"Open Sans",Arial,sans-serif;color:var(--ink);background:var(--white);position:relative}
.slab{font-family:"Arvo",Georgia,serif}
.btn{display:inline-block;background:var(--orange);color:var(--white);font-family:"Arvo",Georgia,serif;font-size:14px;text-transform:uppercase;letter-spacing:.5px;border-radius:3px;text-align:center;box-shadow:0 2px 0 var(--orange-dark)}

/* header */
.site-header{height:125px;position:relative}
.brand{position:absolute;left:99px;top:64px;display:flex;align-items:center;gap:10px}
.brand-mark{width:14px;height:14px;border-radius:50%;background:var(--blue-deep)}
.brand-name{font-family:"Arvo",Georgia,serif;font-size:21px;color:var(--blue-deep)}
.search{position:absolute;left:603px;top:56px;display:flex;align-items:center;gap:24px;font-size:13px;color:#555}
.header-btn{position:absolute;left:745px;top:46px;width:160px;height:41px;line-height:41px}
.socials{position:absolute;left:942px;top:47px;display:flex;gap:12px}
.socials span{width:34px;height:34px;border-radius:50%}
.socials span:nth-child(1){background:#3b5998}
.socials span:nth-child(2){background:#cb2027}
.socials span:nth-child(3){background:#38a1d8}
.socials span:nth-child(4){background:#333}

/* nav */
.main-nav{height:48px;background:linear-gradient(var(--nav-top),var(--nav-bottom));position:relative;color:var(--white);font-size:12px;font-weight:600;text-transform:uppercase}
.main-nav a{position:absolute;top:0;line-height:48px;color:var(--white);text-decoration:none}
.main-nav .prayer{left:930px;width:171px;text-align:center;background:var(--blue);font-size:14px}

/* hero */
.hero{height:531px;position:relative;background:linear-gradient(180deg,#3a2e1c 0%,#8a6a3e 35%,#c79650 55%,#5a3d1f 78%,#120c06 100%);color:var(--white)}
.hero-copy{position:absolute;left:99px;top:170px;width:480px}
.hero h1{font-family:"Arvo",Georgia,serif;font-weight:400;font-size:31px;margin-bottom:14px}
.hero p{font-size:19px;line-height:29px;margin-bottom:22px}
.hero .btn{width:160px;height:44px;line-height:44px}
.dots{position:absolute;left:572px;top:489px;display:flex;gap:6px}
.dots span{width:9px;height:9px;border-radius:50%;background:rgba(255,255,255,.45)}
.dots span:first-child{background:var(--white)}

/* welcome */
.welcome{text-align:center;padding-top:78px;height:314px}
.section-title{font-family:"Arvo",Georgia,serif;font-weight:400;color:var(--blue);text-transform:uppercase;font-size:33px;line-height:40px}
.welcome .section-title{font-size:27px;line-height:32px}
.welcome .section-title span{display:block;font-size:33px;line-height:42px;letter-spacing:1px}
.welcome p{width:830px;margin:26px auto 0;font-size:12.5px;line-height:23px;color:#444}
.welcome p+p{margin-top:12px}

/* activities */
.activities{text-align:center;padding-top:14px}
.activities .lead{font-size:13px;color:#444;margin:14px 0 27px}
.activity-grid{display:grid;grid-template-columns:repeat(4,299px);column-gap:1.33px;row-gap:0}
.activity{height:283px}
.activity .photo{height:198px}
.activity h3{font-family:"Arvo",Georgia,serif;font-weight:400;font-size:14.5px;text-transform:uppercase;margin-top:22px;color:#333}
.activity time{display:block;font-size:11px;color:var(--muted);margin-top:6px}
.activities .btn{margin-top:24px;width:225px;height:47px;line-height:47px}
.ph-a{background:linear-gradient(135deg,#7d5a44,#b8937a 55%,#4f3a2e)}
.ph-b{background:linear-gradient(135deg,#8a3b30,#c9383a 50%,#5a4a3e)}
.ph-c{background:linear-gradient(135deg,#9c8d7a,#c8b9a6 50%,#6e5f50)}
.ph-d{background:linear-gradient(135deg,#6a5142,#c28b7e 50%,#8a6d5a)}

/* message */
.message{position:absolute;left:0;top:1846px;width:1200px;height:393px;background:linear-gradient(180deg,#1f2523 0%,#3a3a34 45%,#2f4a26 80%,#263a1e 100%);color:var(--white);text-align:center}
.message h2{font-family:"Arvo",Georgia,serif;font-weight:400;font-size:33px;padding-top:123px}
.message p{font-size:14px;margin-top:12px}
.message .btn{margin-top:20px;width:156px;height:44px;line-height:44px}

/* news */
.news{position:absolute;left:0;top:2290px;width:1200px;text-align:center}
.news-grid{display:flex;gap:56px;margin:36px 0 0 99px;text-align:left}
.news-item{width:474px}
.news-item .photo{height:256px}
.news-item h3{font-family:"Arvo",Georgia,serif;font-weight:400;font-size:13.5px;text-transform:uppercase;margin-top:28px}
.news-item time{display:block;font-size:11px;color:var(--muted);margin-top:5px}
.news-item p{font-size:11.5px;line-height:22px;color:#444;margin-top:8px}

/* prayer */
.prayer-request{position:absolute;left:0;top:2858px;width:1200px;text-align:center}
.prayer-request p{font-size:15px;line-height:29px;color:#555;margin-top:16px}
.prayer-request .btn{margin-top:22px;width:172px;height:48px;line-height:48px}

/* footer */
.site-footer{position:absolute;left:0;top:3120px;width:1200px;height:291px;background:var(--footer);color:var(--footer-text);font-size:12px}
.footer-col{position:absolute;top:34px}
.footer-col h4{color:var(--white);font-size:12px;font-weight:700;text-transform:uppercase;margin-bottom:14px}
.field{width:300px;height:36px;border:1px solid #2c2c2c;background:#1a1a1a;margin-top:14px;padding-left:12px;line-height:34px;font-size:11px;color:#777}
.footer-col .btn{margin-top:18px;width:119px;height:36px;line-height:36px;font-size:12px}
.mission p{line-height:23px;width:330px}
.network{display:flex;align-items:center;gap:12px;margin-top:28px}
.network .disc{width:38px;height:38px;border-radius:50%;background:var(--white)}
.network span:last-child{font-family:"Open Sans",Arial,sans-serif;font-weight:700;font-size:15px;color:var(--white);line-height:19px;width:150px}
.contact p{line-height:23px}
.contact-line{display:flex;align-items:center;gap:10px;margin-top:10px}
.contact h4.second{margin-top:22px;margin-bottom:8px}
.footer-bar{position:absolute;left:0;top:3411px;width:1200px;height:51px;background:var(--footer-bottom);color:#7a7a7a;font-size:12px}
.footer-bar .copy{position:absolute;left:99px;top:17px}
.footer-bar .connect{position:absolute;right:47px;top:12px;display:flex;align-items:center;gap:10px}
.footer-bar .connect strong{font-size:20px;color:#8a8a8a;font-weight:700}
</style>
</head>
<body>

<header class="site-header">
  <div class="brand"><span class="brand-mark"></span><span class="brand-name">Briar Hollow Gathering Church</span></div>
  <div class="search">
    <svg width="16" height="16" viewBox="0 0 16 16"><circle cx="6.5" cy="6.5" r="5" fill="none" stroke="#444" stroke-width="2"/><line x1="10.5" y1="10.5" x2="15" y2="15" stroke="#444" stroke-width="2"/></svg>
    <span>Search</span>
  </div>
  <a class="btn header-btn">Browse Event</a>
  <div class="socials" aria-label="Social links"><span></span><span></span><span></span><span></span></div>
</header>

<nav class="main-nav">
  <a style="left:122px">Home</a>
  <a style="left:228px">Age Group ▾</a>
  <a style="left:372px">Activities ▾</a>
  <a style="left:513px">Events Calender</a>
  <a style="left:710px">About</a>
  <a style="left:818px">Contact</a>
  <a class="prayer slab">Prayer Request</a>
</nav>

<section class="hero" role="img" aria-label="Sunset sky over a hill with three crosses in silhouette">
  <div class="hero-copy">
    <h1>Briar Hollow Gathering Church</h1>
    <p>Our mission is to reflect the love of God as revealed in Jesus and through His Spirit to make him known by word, sign and deed</p>
    <a class="btn">Join Us Now</a>
  </div>
  <div class="dots"><span></span><span></span><span></span><span></span></div>
</section>

<section class="welcome">
  <h2 class="section-title">Welcome to<span>Briar Hollow Gathering Church</span></h2>
  <p>Since 1958, the Church has had two redevelopment phases and now closely resembles the original 1950s masterplan. Appropriately for the majestic real estate on which it is built, Church stationery and logo depicts 'Light on the Hill'.</p>
  <p>Firstly as the Briar Hollow Methodist Church and from 1977 following the formation of the Gathering Church Network, as the Briar Hollow Gathering Church, it has been a place of community worship in the City of Ashvale and for spreading the good news of the gospel of Jesus.</p>
</section>

<section class="activities">
  <h2 class="section-title">Recent Activities</h2>
  <p class="lead">Our mission is to reflect the love of God as revealed in Jesus and through His Spirit to make him known by word, sign and deed</p>
  <div class="activity-grid">
    <article class="activity"><div class="photo ph-a" role="img" aria-label="Congregation seated in the church hall"></div><h3>Refugee and Asylum Seekers</h3><time>On 27 October 2016</time></article>
    <article class="activity"><div class="photo ph-b" role="img" aria-label="Candle lighting at a red cloth table"></div><h3>Presbytery Annual Meeting</h3><time>On 27 October 2016</time></article>
    <article class="activity"><div class="photo ph-c" role="img" aria-label="Members chatting around a table"></div><h3>2016 Annual Meeting of Council</h3><time>On 27 October 2016</time></article>
    <article class="activity"><div class="photo ph-d" role="img" aria-label="Friends together after the service"></div><h3>Juice During the Sermon</h3><time>On 27 October 2016</time></article>
    <article class="activity"><div class="photo ph-a" role="img" aria-label="Shared lunch table with guests"></div><h3>Wanna Know How to Make...</h3><time>On 27 October 2016</time></article>
    <article class="activity"><div class="photo ph-c" role="img" aria-label="Group gathered in a lounge"></div><h3>Career Times</h3><time>On 27 October 2016</time></article>
    <article class="activity"><div class="photo ph-d" role="img" aria-label="Members talking in the kitchen"></div><h3>News and Notes</h3><time>On 27 October 2016</time></article>
    <article class="activity"><div class="photo ph-b" role="img" aria-label="Guests serving food at a buffet"></div><h3>Juice During the Sermon</h3><time>On 27 October 2016</time></article>
  </div>
  <a class="btn">View More Activities</a>
</section>

<section class="message" role="img" aria-label="Congregation sitting on the lawn at an outdoor gathering">
  <h2>MESSAGE</h2>
  <p>Our mission is to reflect the love of God as revealed in Jesus and through His Spirit to make him known by word, sign and deed</p>
  <a class="btn">Join Us Now</a>
</section>

<section class="news">
  <h2 class="section-title">Recent News</h2>
  <div class="news-grid">
    <article class="news-item"><div class="photo ph-a" role="img" aria-label="Group sharing a meal at a long table"></div><h3>What's wrong with a little sledging?</h3><time>May 17th, 2014</time><p>Many decades ago, in the last century, I played cricket. I think they were short on numbers. I batted for my school and post school. I tried to put bat to ball in the factory team where I worked.</p></article>
    <article class="news-item"><div class="photo ph-c" role="img" aria-label="Members serving food in the hall"></div><h3>What's wrong with a little sledging?</h3><time>May 17th, 2014</time><p>Many decades ago, in the last century, I played cricket. I think they were short on numbers. I batted for my school and post school. I tried to put bat to ball in the factory team where I worked.</p></article>
  </div>
</section>

<section class="prayer-request">
  <h2 class="section-title">Prayer Request</h2>
  <p>Thank you for visiting our website. We would like to invite you to join us for worship at our church on<br>14 Fernleigh Road, Briar Hollow.</p>
  <a class="btn">Send Request</a>
</section>

<footer class="site-footer">
  <div class="footer-col" style="left:99px">
    <h4>Newsletter Signup</h4>
    <p>Connect with our social network</p>
    <div class="field">Enter your name</div>
    <div class="field">Enter your email id</div>
    <a class="btn">Subscribe</a>
  </div>
  <div class="footer-col mission" style="left:475px">
    <h4>Our Mission</h4>
    <p>Our mission is to reflect the love of God as revealed in Jesus and through His Spirit to make him known by word, sign and deed</p>
    <div class="network"><span class="disc"></span><span>Gathering Church Network</span></div>
  </div>
  <div class="footer-col contact" style="left:860px">
    <h4>Contact Info</h4>
    <p>14 Fernleigh Rd, Briar Hollow,<br>WA 6190.</p>
    <div class="contact-line"><svg width="12" height="12" viewBox="0 0 12 12"><path d="M2 1l2 0 1 3-1.5 1a7 7 0 0 0 3.5 3.5L8 7l3 1v2a1 1 0 0 1-1 1A9 9 0 0 1 1 2a1 1 0 0 1 1-1z" fill="#8a8a8a"/></svg><span>(08) 5550 1842</span></div>
    <div class="contact-line"><svg width="12" height="10" viewBox="0 0 12 10"><rect x=".5" y=".5" width="11" height="9" fill="none" stroke="#8a8a8a"/><path d="M.5 .5L6 5l5.5-4.5" fill="none" stroke="#8a8a8a"/></svg><span>office@briarhollowchurch.org</span></div>
    <h4 class="second">Service Times</h4>
    <p>Monday to Friday between 9am to 12noon.</p>
  </div>
</footer>
<div class="footer-bar">
  <span class="copy">Copyright © 2016, Briar Hollow Gathering Church. All rights reserved.</span>
  <span class="connect">Connect with Social media : <strong>Social</strong></span>
</div>

</body>
</html>
```